Tiny Meadow Product Label for Tear-Free Head-to-Toe Wash

Need a bottle label design for a new line of natural products targeting infants and children. Products are Pediatrician-developed and paraben-free, sulfate-free, fragrance-free, and cruelty-free. Design should be clean and have a high-end feel to it. Will need other product labels in Tiny Meadow line designed as well in upcoming projects.

Target Market(s)

Newborn to young elementary age children and their parents

Industry/Entity Type

Cosmetics/Beauty

Font styles to use
Other font styles liked:
• Brand fonts are Jost and Sonorous

Colors

Designer to choose colors to be used in the design.

Requirements
Must have
• Tiny Meadow logo, Pediatrician Developed logo, and a clean high-end feel to it. The label must fit the specialty bottle we will be using (label measurements and diagram will be provided) for the front and back of bottle only (NOT the side labels). It must include our list of ingredients (will provide once designer selected).
Nice to have
• Should stand out on the shelf of other baby products due to it's clean simplicity and high-end feel
Should not have
• too much of a "kiddie" feel to it (targeting the parents not the kids)

```html
<!DOCTYPE html>
<html lang="en">
<head>
<meta charset="UTF-8">
<title>Tiny Meadow – Tear-Free Head-to-Toe Wash Label</title>
<link href="https://fonts.googleapis.com/css2?family=Fredoka:wght@600&family=Poppins:wght@500&display=swap" rel="stylesheet">
<style>
  :root {
    --page: #ffffff;
    --label-gold: #9b7430;
    --photo-light: #b18a48;
    --photo-dark: #8f6a2a;
    --ink-white: #ffffff;
  }
  * { margin: 0; padding: 0; box-sizing: border-box; }
  html, body {
    width: 1200px;
    height: 1200px;
    overflow: hidden;
    background: var(--page);
  }
  .canvas {
    position: relative;
    width: 1200px;
    height: 1200px;
  }
  .label {
    position: absolute;
    left: 250px;
    top: 160px;
    width: 700px;
    height: 880px;
    background: var(--label-gold);
    border-radius: 350px 350px 0 0;
    overflow: hidden;
  }
  .label__photo {
    position: absolute;
    left: 0;
    top: 250px;
    width: 100%;
    height: 630px;
    background:
      radial-gradient(ellipse at 40% 35%, var(--photo-light) 0%, rgba(177,138,72,0) 60%),
      radial-gradient(ellipse at 75% 70%, var(--photo-light) 0%, rgba(177,138,72,0) 55%),
      linear-gradient(180deg, var(--label-gold) 0%, var(--photo-dark) 100%);
    opacity: 0.85;
  }
  .brand-badge {
    position: absolute;
    left: 50%;
    top: 90px;
    width: 144px;
    height: 144px;
    margin-left: -72px;
    border: 3px solid var(--ink-white);
    border-radius: 50%;
    display: flex;
    align-items: center;
    justify-content: center;
    text-align: center;
    font-family: "Fredoka", sans-serif;
    font-weight: 600;
    font-size: 22px;
    line-height: 1.1;
    color: var(--ink-white);
    letter-spacing: 1px;
  }
  .product-name {
    position: absolute;
    left: 0;
    width: 100%;
    top: 340px;
    text-align: center;
    font-family: "Fredoka", sans-serif;
    font-weight: 600;
    font-size: 118px;
    line-height: 1.08;
    color: var(--ink-white);
  }
  .wave {
    position: absolute;
    left: 185px;
    top: 665px;
    width: 330px;
    height: 50px;
  }
  .claims {
    position: absolute;
    left: 146px;
    top: 752px;
    width: 440px;
    display: grid;
    grid-template-columns: 294px 1fr;
    row-gap: 12px;
    font-family: "Poppins", sans-serif;
    font-weight: 500;
    font-size: 18px;
    color: var(--ink-white);
    list-style: none;
  }
</style>
</head>
<body>
<main class="canvas">
  <section class="label">
    <div class="label__photo" role="img" aria-label="Soft photo of a smiling baby at bath time, toned in warm gold"></div>

    <div class="brand-badge">Tiny<br>Meadow</div>

    <h1 class="product-name">Tiny<br>Meadow</h1>

    <svg class="wave" viewBox="0 0 330 50" aria-hidden="true">
      <path d="M0 38 C 70 8, 130 8, 170 24 S 270 44, 330 14" fill="none" stroke="var(--ink-white)" stroke-width="5" stroke-linecap="round"/>
    </svg>

    <ul class="claims">
      <li>Paraben-free</li>
      <li>Sulfate-free</li>
      <li>Fragrance-free</li>
      <li>Cruelty-free</li>
    </ul>
  </section>
</main>
</body>
</html>
```